Zestora - Landing Page

Need a landing page for a journal app. The app is based on a retrospective board, where each journal entry is split into 3 sections: "What went well", "What Didn't Go Well" and "Things To Try".
The landing page should match the style of all modern web application landing pages. Think Brint, Tivalo, Mirvane. I've included screenshots of the app.
One feature that I want to highlight that is not ready yet, is an AI coach. It will offer insights based on the history of the user's journal entries
1 page

```html
<!DOCTYPE html>
<html lang="en">
<head>
<meta charset="utf-8">
<title>Zestora – Journal App Landing Page</title>
<link rel="stylesheet" href="https://fonts.googleapis.com/css2?family=Quicksand:wght@400;500;600;700&family=Lato:wght@400;700&display=swap">
<style>
:root{
  --blue:#0b6fbb;
  --blue-dark:#085a98;
  --blue-soft:#eef4fb;
  --ink:#1d1d1f;
  --text:#555b63;
  --muted:#8a9099;
  --line:#d9dee5;
  --gray-bg:#f3f3f3;
  --navy:#1e2838;
  --white:#ffffff;
  --green:#27b36a;
}
*{box-sizing:border-box;margin:0;padding:0}
html,body{width:1200px;height:4684px;overflow:hidden}
body{position:relative;font-family:"Quicksand",sans-serif;color:var(--ink);background:var(--white)}
.abs{position:absolute}
a{color:inherit;text-decoration:none}

/* header */
.logo{font-family:"Quicksand",sans-serif;font-weight:700;color:var(--blue);letter-spacing:1px}
.site-logo{left:110px;top:52px;font-size:32px}
.nav{left:415px;top:56px;display:flex;gap:0;align-items:center;font-size:14px;font-weight:500;color:var(--ink)}
.nav a{padding:6px 12px}
.nav .active{background:var(--blue);color:var(--white);border-radius:16px;padding:6px 16px}
.nav .caret{display:inline-block;margin-left:5px;border:4px solid transparent;border-top:5px solid var(--ink);vertical-align:-4px}
.nav-divider{left:900px;top:52px;width:1px;height:36px;background:var(--line)}
.btn{display:inline-flex;align-items:center;justify-content:center;border-radius:24px;font-family:"Quicksand",sans-serif;font-weight:600;font-size:14px}
.btn-outline{border:1.5px solid var(--blue);color:var(--ink);background:var(--white)}
.btn-solid{background:var(--blue);color:var(--white)}
.btn-ghost{border:1.5px solid var(--white);color:var(--white)}
.login{left:934px;top:50px;width:155px;height:42px;font-size:15px;font-weight:500}

/* hero */
.hero-dots{left:600px;top:150px;width:620px;height:520px;background:radial-gradient(ellipse at 60% 45%,rgba(11,111,187,.09),rgba(11,111,187,0) 65%)}
.eyebrow{left:0;width:1200px;top:166px;text-align:center;color:var(--blue);font-size:22px;font-weight:500;letter-spacing:.5px}
.hero-title{left:0;width:1200px;top:202px;text-align:center;font-size:40px;font-weight:700;line-height:50px;letter-spacing:.5px}
.hero-copy{left:240px;width:720px;top:314px;text-align:center;font-size:18px;line-height:28px;color:var(--ink);font-weight:500}
.hero-btn{left:531px;top:394px;width:138px;height:42px}

.blue-wave{left:0;top:0;width:1200px;height:1500px}

/* app mockup */
.app{left:100px;top:491px;width:1000px;height:560px;background:#f7f7f7;border:5px solid var(--white);border-radius:18px;box-shadow:0 10px 30px rgba(0,0,0,.18);overflow:hidden;font-family:"Lato",sans-serif}
.app-side{position:absolute;left:0;top:0;width:42px;height:100%;background:var(--navy)}
.app-side i{position:absolute;left:15px;width:12px;height:10px;border:2px solid #c6cdd8;border-radius:2px}
.app-side .av{left:11px;top:520px;width:20px;height:20px;border-radius:50%;background:#c6cdd8;border:none}
.side-mark{position:absolute;left:13px;top:8px;width:16px;height:14px;background:var(--green);border-radius:3px}
.app-title{position:absolute;left:107px;top:10px;font-size:15px;font-weight:700}
.app-date{position:absolute;left:112px;top:42px;font-size:10px;color:#333}
.tag{position:absolute;left:242px;top:39px;padding:2px 10px;border-radius:10px;background:var(--green);color:var(--white);font-size:9px}
.col{position:absolute;top:90px;width:247px;height:430px;border:1px solid #dcdcdc;border-radius:4px;background:#f4f4f4}
.col h4{font-size:10px;font-weight:400;padding:12px 0 0 32px;position:relative}
.col h4:before{content:"";position:absolute;left:14px;top:12px;width:10px;height:9px;background:var(--blue);border-radius:2px}
.editor{position:absolute;left:9px;top:40px;right:9px;bottom:10px;border:1px solid #cfcfcf;background:#f1f1f1}
.toolbar{height:40px;border-bottom:1px solid #cfcfcf;background:#e9e9e9;padding:6px 8px;font-size:9px;line-height:14px;color:#333;letter-spacing:1px}
.editor ul{padding:10px 12px 0 30px;font-size:10.5px;line-height:16px;color:#222}
.float-tag{background:var(--white);color:var(--blue);border-radius:26px;box-shadow:0 4px 14px rgba(0,0,0,.15);font-size:15px;font-weight:500;display:flex;align-items:center;justify-content:center}

/* features */
.features-title{left:148px;top:1230px;font-size:40px;color:var(--white);letter-spacing:.5px}
.features-title b{font-weight:700}
.features-title span{font-weight:500}
.features-rule{left:510px;top:1140px;width:1px;height:270px;background:rgba(255,255,255,.35)}
.features-list{left:560px;top:1138px;width:500px;list-style:none;color:var(--white);font-size:16px;line-height:25px;font-weight:500}
.features-list li{position:relative;padding-left:24px;margin-bottom:11px}
.features-list li:before{content:"";position:absolute;left:0;top:10px;width:5px;height:5px;border-radius:50%;background:var(--white)}
.features-btn{left:560px;top:1398px;width:136px;height:44px}

/* section headings */
.sec-title{font-size:42px;letter-spacing:.5px;line-height:52px}
.sec-title b{font-weight:700}
.sec-title span{font-weight:400}
.underline{height:4px;width:74px;background:var(--blue);border-radius:2px}
.whatwedo-title{left:0;width:1200px;top:1610px;text-align:center}

/* cards */
.card{top:1713px;width:304px;height:418px;background:var(--blue-soft);border-radius:10px;padding:34px 20px 0}
.card svg{display:block;width:62px;height:62px}
.card h3{font-size:17px;font-weight:600;margin:16px 0 8px}
.card p{font-size:15px;line-height:22px;color:var(--text);font-weight:500;margin-bottom:15px}
.card .btn{width:134px;height:42px;margin-top:4px}

/* choose */
.choose-bg{left:0;top:2254px;width:1200px;height:564px;background:var(--gray-bg)}
.body-copy{font-size:15px;line-height:24px;color:var(--text);font-weight:500}
.shot{background:var(--white);border:3px solid #9fb9d6;border-radius:18px;overflow:hidden;box-shadow:0 6px 20px rgba(0,0,0,.1);font-family:"Lato",sans-serif}

/* testimonial */
.photo-ring{left:112px;top:2940px;width:446px;height:422px;border-radius:50%;background:#eef3fa}
.photo{left:150px;top:2960px;width:370px;height:370px;border-radius:50%;background:linear-gradient(135deg,#3c4a57 0%,#8d99a5 45%,#c7ccd1 70%,#6f7b86 100%)}
.play{left:312px;top:3122px;width:42px;height:42px;border-radius:50%;background:rgba(255,255,255,.85)}
.name-pill{left:304px;top:3300px;width:276px;height:52px;background:var(--white);border-radius:26px;box-shadow:0 4px 16px rgba(0,0,0,.08);display:flex;align-items:center;padding-left:10px;font-size:16px;font-weight:600}
.name-pill i{width:38px;height:38px;border-radius:50%;background:var(--blue);margin-right:22px;position:relative}
.name-pill i:after{content:"";position:absolute;left:13px;top:9px;width:12px;height:12px;border-radius:50%;background:var(--white);box-shadow:0 12px 0 1px var(--white)}
.name-pill small{font-size:12px;font-weight:500;margin-left:4px}

/* cta */
.cta-band{left:0;top:4090px;width:1200px;height:223px;background:#eaf2fb}
.cta{left:42px;top:3969px;width:1114px;height:344px;border-radius:172px;background:linear-gradient(120deg,#1879c4 0%,#0b6fbb 45%,#3b8fd0 75%,#0a62a8 100%);color:var(--white);text-align:center}
.cta h2{font-size:42px;letter-spacing:.5px;margin-top:60px}
.cta h2 b{font-weight:700}.cta h2 span{font-weight:400}
.cta p{width:900px;margin:22px auto 0;font-size:15px;line-height:24px;font-weight:500}
.cta .btn{width:158px;height:44px;margin-top:32px}

/* footer */
.footer-logo{left:110px;top:4477px;font-size:40px}
.fcol h5{font-size:16px;font-weight:700;letter-spacing:.5px;margin-bottom:22px}
.fcol ul{list-style:none;font-size:14px;font-weight:500}
.fcol li{position:relative;padding-left:30px;height:40px}
.fcol li:before{content:"";position:absolute;left:0;top:7px;width:5px;height:5px;border-radius:50%;background:var(--blue)}
.contact li{display:flex;align-items:flex-start;padding:0;height:auto;margin-bottom:20px;line-height:20px}
.contact li:before{display:none}
.contact i{flex:none;width:32px;height:32px;border-radius:50%;background:var(--blue-soft);margin-right:22px;display:flex;align-items:center;justify-content:center}
.footer-rule{left:110px;top:4618px;width:980px;height:1px;background:var(--line)}
.copyright{left:0;width:1200px;top:4642px;text-align:center;font-size:13px;font-weight:500;color:#444}
.social{top:4634px;width:34px;height:34px;border-radius:50%;background:var(--blue-soft)}
.social.on{background:var(--blue)}
</style>
</head>
<body>

<!-- blue background wave -->
<svg class="abs blue-wave" viewBox="0 0 1200 1500" aria-hidden="true">
  <path d="M0 690 C 120 760 170 900 330 960 C 480 1010 600 1030 760 1010 C 950 985 1080 840 1200 720 L1200 1500 L0 1500 Z" fill="#0b6fbb"/>
</svg>
<div class="abs hero-dots" aria-hidden="true"></div>

<!-- header -->
<header>
  <div class="abs logo site-logo">ZESTORA</div>
  <nav class="abs nav">
    <a class="active">Home</a><a>About Us</a><a>Our Features<span class="caret"></span></a><a>Resources</a><a>Contact</a>
  </nav>
  <div class="abs nav-divider"></div>
  <a class="abs btn btn-outline login">Customer Login</a>
</header>

<!-- hero -->
<section class="hero">
  <p class="abs eyebrow">WELCOME TO</p>
  <h1 class="abs hero-title">WHAT WENT WELL. WHAT DIDN’T<br>GO WELL. THINGS TO TRY</h1>
  <p class="abs hero-copy">Lorem ipsum dolor sit amet, consectetur adipiscing elit, sed do eiusmod tempor incididunt ut labore et dolore magna aliqua.</p>
  <a class="abs btn btn-solid hero-btn">Get Started</a>

  <div class="abs app">
    <div class="app-side">
      <span class="side-mark"></span>
      <i style="top:52px"></i><i style="top:78px"></i><i style="top:104px"></i>
      <i class="av"></i>
    </div>
    <div class="app-title">Entry</div>
    <div class="app-date">▦ Thu Aug 22 2024 ⌄</div>
    <span class="tag">Gym</span>

    <div class="col" style="left:113px">
      <h4>What Went Well?</h4>
      <div class="editor">
        <div class="toolbar">Normal ⇕ &nbsp;<b>B</b> <i>I</i> <u>U</u> S ”<br>☰ ☰ ☰ ☰ &nbsp;T</div>
        <ul><li>Completed all scheduled workouts this week.</li><li>Increased bench press weight by 10 pounds.</li><li>Maintained consistent energy levels throughout sessions.</li></ul>
      </div>
    </div>
    <div class="col" style="left:397px">
      <h4>What Didn't Go Well?</h4>
      <div class="editor">
        <div class="toolbar">Normal ⇕ &nbsp;<b>B</b> <i>I</i> <u>U</u> S ”<br>☰ ☰ ☰ ☰ &nbsp;T</div>
        <ul><li>Struggled with form on deadlifts, leading to lower back discomfort.</li><li>Missed two stretching sessions after workouts.</li><li>Skipped meal prep, resulting in inconsistent nutrition.</li></ul>
      </div>
    </div>
    <div class="col" style="left:680px">
      <h4>Things To Try</h4>
      <div class="editor">
        <div class="toolbar">Normal ⇕ &nbsp;<b>B</b> <i>I</i> <u>U</u> S ”<br>☰ ☰ ☰ ☰ &nbsp;T</div>
        <ul><li>Focus on deadlift form by lowering the weight and reviewing proper technique.</li><li>Set reminders for post-workout stretching to prevent muscle tightness.</li><li>Dedicate Sunday evenings to meal prep to ensure a balanced diet.</li></ul>
      </div>
    </div>
  </div>

  <div class="abs float-tag" style="left:993px;top:607px;width:167px;height:48px">What went well</div>
  <div class="abs float-tag" style="left:25px;top:827px;width:155px;height:50px">Things To Try</div>
  <div class="abs float-tag" style="left:407px;top:1029px;width:202px;height:48px">What Didn't Go Well</div>
</section>

<!-- features -->
<section class="features">
  <h2 class="abs features-title"><b>OUR</b> <span>FEATURES</span></h2>
  <div class="abs features-rule"></div>
  <ul class="abs features-list">
    <li>Lorem ipsum dolor sit amet, consectetur adipiscing elit, sed do eiusmod tempor incididuntea.</li>
    <li>Lorem ipsum dolor sit amet, consectetur adipiscing elit, sed tempor incididuntea.</li>
    <li>Lorem ipsum dolor sit amet, consectetur adipiscing elit, sed do eiusmod tempor incididuntea.</li>
    <li>Lorem ipsum dolor sit amet, consectetur adipiscing elit, sed tempor incididuntea.</li>
  </ul>
  <a class="abs btn btn-ghost features-btn">Get Started</a>
</section>

<!-- what we do -->
<section class="what-we-do">
  <h2 class="abs sec-title whatwedo-title"><b>WHAT</b> <span>WE DO</span></h2>
  <div class="abs underline" style="left:563px;top:1664px"></div>

  <article class="abs card" style="left:111px">
    <svg viewBox="0 0 62 62" fill="none" stroke="#0b6fbb" stroke-width="2"><circle cx="31" cy="16" r="8"/><circle cx="17" cy="22" r="5"/><circle cx="45" cy="22" r="5"/><path d="M20 36c3-6 19-6 22 0"/><path d="M6 44l12-6 10 4h10l-2 5H26"/><path d="M56 44l-10-4-8 2"/><path d="M6 50l10 6h14l22-10"/></svg>
    <h3>Lorem ipsum dolor</h3>
    <p>Lorem ipsum dolor sit amet, consec adipiscing elit, sed do eiusmod tem incididunt ut labore et dolore magna aliqua.</p>
    <p>Lorem ipsum dolor sit amet, consec adipiscing elit, sed do eiusmod tem incididunt ut labore et dolore magna aliqua.</p>
    <a class="btn btn-outline">Learn More</a>
  </article>
  <article class="abs card" style="left:447px">
    <svg viewBox="0 0 62 62" fill="none" stroke="#0b6fbb" stroke-width="2"><rect x="6" y="8" width="50" height="36" rx="2"/><rect x="12" y="14" width="38" height="24"/><path d="M18 32l8-8 6 5 10-10"/><path d="M24 44v8M38 44v8M16 54h30"/></svg>
    <h3>Lorem ipsum dolor</h3>
    <p>Lorem ipsum dolor sit amet, consec adipiscing elit, sed do eiusmod tem incididunt ut labore et dolore magna aliqua.</p>
    <p>Lorem ipsum dolor sit amet, consec adipiscing elit, sed do eiusmod tem incididunt ut labore et dolore magna aliqua.</p>
    <a class="btn btn-solid">Learn More</a>
  </article>
  <article class="abs card" style="left:784px">
    <svg viewBox="0 0 62 62" fill="none" stroke="#0b6fbb" stroke-width="2"><rect x="6" y="8" width="50" height="46" rx="3"/><path d="M6 16h50"/><circle cx="31" cy="35" r="8"/><circle cx="31" cy="35" r="3"/><path d="M31 22v4M31 44v4M18 35h4M40 35h4M22 26l3 3M37 41l3 3M40 26l-3 3M22 44l3-3"/></svg>
    <h3>Lorem ipsum dolor</h3>
    <p>Lorem ipsum dolor sit amet, consec adipiscing elit, sed do eiusmod tem incididunt ut labore et dolore magna aliqua.</p>
    <p>Lorem ipsum dolor sit amet, consec adipiscing elit, sed do eiusmod tem incididunt ut labore et dolore magna aliqua.</p>
    <a class="btn btn-outline">Learn More</a>
  </article>
</section>

<!-- choose how you work -->
<section class="choose">
  <div class="abs choose-bg"></div>
  <h2 class="abs sec-title" style="left:111px;top:2326px"><b>CHOOSE HOW YOU</b><br><span>WANT TO WORK</span></h2>
  <div class="abs underline" style="left:111px;top:2432px"></div>
  <p class="abs body-copy" style="left:111px;top:2466px;width:435px">Lorem ipsum dolor sit amet, consectetur adipiscing elit, sed do eiusmod tempor incididunt ut labore et dolore magna aliqua. Ut enim ad minim veniam, quis nostrud exercitation ullamco laboris nisi ut aliquip ex ea commodo consequat. Duis aute irure dolor in reprehenderit in voluptate velit esse cillum dolore eu fugiat nulla pariatur. Excepteur sint occaecat cupidatat non proident, sunt in culpa qui officia deserunt mollit anim id est laborumea.</p>
  <a class="abs btn btn-solid" style="left:111px;top:2693px;width:157px;height:44px">Start For Free</a>

  <div class="abs shot" style="left:598px;top:2344px;width:492px;height:386px">
    <div style="position:absolute;left:0;top:0;width:18px;height:100%;background:var(--navy)"></div>
    <div style="position:absolute;left:80px;top:30px;padding:3px 8px;border:1px solid #ccc;border-radius:4px;font-size:7px">+ Add New</div>
    <div style="position:absolute;left:434px;top:30px;padding:2px 8px;border-radius:8px;background:var(--green);color:#fff;font-size:6px">Gym</div>
    <div style="position:absolute;left:78px;top:60px;width:396px;height:250px;border:1px solid #e2e2e2;padding:10px;font-size:7px;line-height:11px;color:#333">
      <b>Thu Aug 22 2024</b><br><span style="color:#999">What Went Well</span><br>Completed all scheduled workouts this week.<br>Increased bench press weight by 10 pounds.<br><span style="color:#999">What Didn't Go Well</span><br>Struggled with form on deadlifts.<br>Skipped meal prep twice.<br><span style="color:#999">Things To Try</span><br>Review deadlift form videos.<br>Plan meals every Sunday.
    </div>
    <div style="position:absolute;left:78px;top:320px;width:396px;height:70px;border:1px solid #e2e2e2;padding:10px;font-size:7px;line-height:11px;color:#333">
      <b>Tue Aug 20 2024</b><br><span style="color:#999">What Went Well</span><br>Added 15 pounds to squats.
    </div>
  </div>
</section>

<!-- testimonial -->
<section class="testimonial">
  <div class="abs photo-ring"></div>
  <div class="abs photo" role="img" aria-label="Portrait photo of a smiling businessman in a grey suit with arms crossed"></div>
  <div class="abs play"><svg viewBox="0 0 42 42" width="42" height="42"><path d="M17 13l12 8-12 8z" fill="#8a9099"/></svg></div>
  <div class="abs name-pill"><i></i>DANIEL REYES,<small>CEO</small></div>

  <h2 class="abs sec-title" style="left:633px;top:2928px"><b>WHAT OUR</b><br><span>CLIENTS SAY</span></h2>
  <div class="abs underline" style="left:633px;top:3035px"></div>
  <p class="abs body-copy" style="left:633px;top:3072px;width:460px">Lorem ipsum dolor sit amet, consectetur adipiscing elit, sed do eiusmod tempor incididunt ut labore et dolore magna aliqua. Ut enim ad minim veniam, quis nostrud exercitation ullamco laboris nisi ut aliquip ex ea commodo consequat. Duis aute irure dolor in reprehenderit in voluptate velit esse cillum dolore eu fugiat nulla pariatur. Excepteur sint occaecat cupidatat non proident, sunt in culpa qui officia deserunt mollit anim id est laborumea.</p>
  <a class="abs btn btn-solid" style="left:633px;top:3300px;width:252px;height:42px">See more customer stories</a>
</section>

<!-- AI coach -->
<section class="ai-coach">
  <h2 class="abs sec-title" style="left:111px;top:3498px"><b>AI</b> <span>COACH</span></h2>
  <div class="abs underline" style="left:111px;top:3552px"></div>
  <p class="abs body-copy" style="left:111px;top:3578px;width:435px">Lorem ipsum dolor sit amet, consectetur adipiscing elit, sed do eiusmod tempor incididunt ut labore et dolore magna aliqua. Ut enim ad minim veniam, quis nostrud exercitation ullamco laboris nisi ut aliquip ex ea commodo consequat. Duis aute irure dolor in reprehenderit in voluptate velit esse cillum dolore eu fugiat nulla pariatur. Excepteur sint occaecat cupidatat non proidentea.</p>
  <a class="abs btn btn-solid" style="left:111px;top:3779px;width:157px;height:44px">Start For Free</a>

  <div class="abs shot" style="left:598px;top:3472px;width:492px;height:383px;background:#f6f8fb">
    <svg width="492" height="383" viewBox="0 0 492 383">
      <rect x="0" y="8" width="44" height="220" rx="20" fill="#7fb0dc"/>
      <rect x="64" y="22" width="150" height="8" rx="3" fill="#dde3ea"/>
      <rect x="370" y="18" width="60" height="14" rx="6" fill="#eaeef3"/>
      <circle cx="458" cy="25" r="10" fill="#7fb0dc"/>
      <rect x="64" y="62" width="180" height="100" rx="6" fill="#fff"/>
      <rect x="260" y="62" width="90" height="100" rx="6" fill="#fff"/>
      <rect x="364" y="62" width="110" height="200" rx="6" fill="#fff"/>
      <rect x="64" y="172" width="90" height="90" rx="6" fill="#fff"/>
      <rect x="160" y="172" width="190" height="90" rx="6" fill="#fff"/>
      <g fill="#7fb0dc"><rect x="176" y="228" width="10" height="24"/><rect x="198" y="212" width="10" height="40"/><rect x="220" y="222" width="10" height="30"/><rect x="242" y="218" width="10" height="34"/><rect x="264" y="200" width="10" height="52"/><rect x="286" y="226" width="10" height="26"/><rect x="308" y="206" width="10" height="46"/></g>
      <rect x="364" y="272" width="110" height="90" rx="4" fill="#7fb0dc"/>
      <rect x="64" y="272" width="290" height="90" rx="6" fill="#fff"/>
      <g fill="#e3e8ee"><rect x="76" y="290" width="260" height="6"/><rect x="76" y="312" width="260" height="6"/><rect x="76" y="334" width="260" height="6"/></g>
    </svg>
  </div>
</section>

<!-- call to action -->
<section>
  <div class="abs cta-band"></div>
  <div class="abs cta" role="img" aria-label="Blue-tinted photo banner with a call to action">
    <h2><b>GET</b> <span>STARTED</span></h2>
    <p>Lorem ipsum dolor sit amet, consectetur adipiscing elit, sed do eiusmod tempor incididunt ut labore et dolore magna aliqua. Ut enim ad minim veniam, quis nostrud exercitation ullamco laboris nisi ut aliquip ex ea commodo consequat. Duis aute irure dolor in reprehenderit in voluptate velit esse cillum dolore eu fugiatea.</p>
    <a class="btn btn-ghost">Start For Free</a>
  </div>
</section>

<!-- footer -->
<footer>
  <div class="abs logo footer-logo">ZESTORA</div>
  <div class="abs fcol" style="left:380px;top:4374px">
    <h5>NAVIGATION</h5>
    <ul><li>Home</li><li>About Us</li><li>Our Features</li><li>Resources</li><li>Contact</li></ul>
  </div>
  <div class="abs fcol" style="left:570px;top:4374px">
    <h5>QUICK LINKS</h5>
    <ul><li>Site Map</li><li>Privacy Policy</li><li>Terms &amp; Conditions</li><li>Disclaimer</li></ul>
  </div>
  <div class="abs fcol contact" style="left:796px;top:4374px;width:300px">
    <h5>CONTACT US</h5>
    <ul>
      <li><i><svg width="14" height="14" viewBox="0 0 14 14"><path d="M7 1a4 4 0 0 1 4 4c0 3-4 8-4 8S3 8 3 5a4 4 0 0 1 4-4z" fill="#0b6fbb"/><circle cx="7" cy="5" r="1.5" fill="#fff"/></svg></i>27 Larkfield Row, Brookhaven,<br>United States</li>
      <li><i><svg width="14" height="14" viewBox="0 0 14 14"><rect x="1" y="3" width="12" height="9" rx="1" fill="#0b6fbb"/><path d="M1 4l6 4 6-4" stroke="#fff" fill="none"/></svg></i>info@zestora.com</li>
      <li><i><svg width="14" height="14" viewBox="0 0 14 14"><path d="M3 1l2.5 2.5-1.5 2a7 7 0 0 0 4.5 4.5l2-1.5L13 11l-2 2C6 13 1 8 1 3z" fill="#0b6fbb"/></svg></i>+1 (555) 014 2290</li>
    </ul>
  </div>
  <div class="abs footer-rule"></div>
  <p class="abs copyright">© 2024 ZESTORA &nbsp;| &nbsp;All Rights Reserved</p>
  <span class="abs social on" style="left:923px"></span>
  <span class="abs social" style="left:966px"></span>
  <span class="abs social" style="left:1009px"></span>
  <span class="abs social" style="left:1052px"></span>
</footer>

</body>
</html>
```